Website design with eCommerce for revolutionary new product in the manufacturing industry.

We need a website designed for a precision manufacturing company based in the suburbs of Minneapolis, Minnesota called Velkrin Manufacturing. We have a revolutionary new product, the TARN LOCK, to introduce and sell through an eCommerce storefront. The website would include company information, product information, and the storefront. Green is a color that represents Velkrin Manufacturing. The final design should communicate that we exclusively offer premium products at a premium price. The design should also let the customer know they are the focus of our work.

Target Market(s)

Machinists and machine shops

Industry/Entity Type

Manufacturing and machine shops

Coding

Coded - Design and coding required

Font styles to use
Sans Serif

Colors
59FF00
82FF00
B8FF75
E3FFCB
F4FFEA

Requirements
Must have
• eCommerce storefront, Made in USA references
Nice to have
• Home page, TARN LOCK Product page, About Us, Capabilities, Contact, etc.
Should not have
• Should not be too much text and reading.

```html
<!DOCTYPE html>
<html lang="en">
<head>
<meta charset="utf-8">
<title>Gallery – TARN LOCK</title>
<link href="https://fonts.googleapis.com/css2?family=Audiowide&family=Poppins:wght@400;500;600;700&display=swap" rel="stylesheet">
<style>
:root{
  --green:#59ff00;
  --bg:#141414;
  --bg-dark:#0c0c0c;
  --nav:#1a1a1a;
  --field:#262626;
  --text:#ffffff;
  --muted:#cfcfcf;
}
*{margin:0;padding:0;box-sizing:border-box}
html,body{width:723px;height:1200px;overflow:hidden;background:var(--bg)}
body{position:relative;font-family:'Poppins',sans-serif;color:var(--text)}
.abs{position:absolute}
.display{font-family:'Audiowide',sans-serif}

.nav{left:0;top:0;width:723px;height:46px;background:var(--nav)}
.brand{left:54px;top:13px;font-weight:700;font-size:15px;letter-spacing:.5px;line-height:20px}
.menu{left:192px;top:19px;display:flex;gap:11.5px;font-size:7px;font-weight:500;white-space:nowrap}
.menu .active{color:var(--green)}
.nav-cta{left:660px;top:0;width:63px;height:46px;background:var(--green);color:#111;font-size:7.5px;font-weight:600;display:flex;align-items:center;justify-content:center}

.hero{left:0;top:46px;width:723px;height:234px;background:
  radial-gradient(ellipse at 30% 30%,rgba(210,205,198,.55),transparent 60%),
  radial-gradient(ellipse at 80% 60%,rgba(190,185,178,.45),transparent 55%),
  linear-gradient(160deg,#6d6a66,#3c3a38 55%,#5b5752)}
.hero-title{left:0;top:116px;width:723px;text-align:center;font-size:38px;letter-spacing:1px}
.hero-band{left:0;top:160px}

.section-title{left:0;top:308px;width:723px;text-align:center;font-size:22px;letter-spacing:.5px}
.rule{left:336px;top:340px;width:51px;height:2px;background:var(--green)}
.lead{left:0;top:356px;width:723px;text-align:center;font-size:8.6px;color:var(--muted)}

.tile{border-radius:6px}
.t-metal{background:radial-gradient(circle at 30% 35%,#e4e4e2 0,#b8b5ae 35%,transparent 60%),linear-gradient(135deg,#cbb07c,#a88a55 60%,#8a6c3e)}
.t-dark{background:radial-gradient(ellipse at 75% 45%,#e8e8e8 0,#8d8d8d 25%,transparent 50%),linear-gradient(135deg,#6f6f6f,#2e2e2e 55%,#4b4b4b)}
.t-tri{background:radial-gradient(circle at 50% 50%,#d4d2ce 0,#9c978e 45%,#6b6356 100%)}
.t-pins{background:radial-gradient(ellipse at 50% 30%,#dcdcdc 0,#9c9ea1 35%,#4e5053 100%)}
.t-chips{background:radial-gradient(ellipse at 45% 50%,#d8d8d8 0,#9a9a9a 40%,#4a4a4a 100%)}
.t-holes{background:radial-gradient(circle at 50% 45%,#ededed 0,#a8a8a8 35%,#5d5d5d 100%)}
.t-brass{background:radial-gradient(ellipse at 35% 30%,#e7c27a 0,#c89a52 25%,transparent 50%),radial-gradient(ellipse at 75% 75%,#e0b96e 0,#b58a44 22%,transparent 45%),linear-gradient(135deg,#2456a8,#17438d)}
.t-coil{background:radial-gradient(ellipse at 50% 50%,#3f66b8 0,#23457f 35%,transparent 60%),linear-gradient(135deg,#c9ccd2,#8f98a8 60%,#b6bcc6)}

.load{left:328px;top:781px;width:67px;height:24px;background:#2a2a2a;border-radius:3px;font-size:7.5px;font-weight:700;display:flex;align-items:center;justify-content:center}

.footer{left:0;top:866px;width:723px;height:334px;background:var(--bg-dark)}
.foot-brand{left:54px;top:900px;font-weight:700;font-size:15px;letter-spacing:.5px}
.foot-about{left:214px;top:895px;font-size:9px;line-height:13.4px;color:var(--muted)}
.callband{left:0;top:866px}
.call-icon{left:474px;top:902px;width:28px;height:27px;background:#111;border-radius:2px;display:flex;align-items:center;justify-content:center}
.call-label{left:509px;top:909px;font-size:8px;font-weight:600;color:#111}
.call-num{left:544px;top:902px;font-size:16px;font-weight:600;color:#111}

.col-head{top:989px;font-size:10px;letter-spacing:.3px}
.links{left:87px;top:1011px;font-size:7px;line-height:13.4px;color:var(--muted);list-style:none}
.social{left:223px;display:flex;align-items:center;gap:5px;font-size:7px;color:var(--muted)}
.social i{display:block;width:15px;height:15px;background:#242424;border-radius:2px}
.contact-item{left:338px;font-size:7.8px;line-height:11.5px;color:var(--muted)}
.contact-item svg{position:absolute;left:0;top:1px}
.contact-item div{margin-left:13px}
.field{left:484px;width:155px;height:20px;background:var(--field);border-radius:2px;font-size:7px;color:#bbb;padding-left:9px;display:flex;align-items:center}
.submit{left:484px;top:1094px;width:54px;height:20px;background:#fff;color:#111;font-size:7.5px;font-weight:600;border-radius:2px;display:flex;align-items:center;justify-content:center}
.divider{left:54px;top:1160px;width:615px;height:1px;background:#2c2c2c}
.copy{left:0;top:1175px;width:723px;text-align:center;font-size:7.5px;font-weight:600}
.top-btn{left:681px;top:1148px;width:28px;height:27px;background:var(--green);display:flex;align-items:center;justify-content:center}
</style>
</head>
<body>

<header class="abs nav">
  <div class="abs brand">TARN LOCK</div>
  <nav class="abs menu">
    <span>WHY VELKRIN MANUFACTURING?</span><span>WHAT WE DO</span><span>HOW WE MAKE IT BETTER</span><span>CAPABILITIES</span><span class="active">GALLERY</span><span>ABOUT US</span><span>WISDOM</span>
  </nav>
  <div class="abs nav-cta">CONTACT</div>
</header>

<section class="abs hero" role="img" aria-label="Rows of machined triangular metal parts on a wooden surface"></section>
<svg class="abs hero-band" width="723" height="122" viewBox="0 0 723 122">
  <polygon points="0,122 723,8 723,38 0,122" fill="#59ff00"/>
  <polygon points="0,122 723,38 723,122" fill="#141414"/>
</svg>
<h1 class="abs hero-title display">GALLERY</h1>

<h2 class="abs section-title display">OUR PROJECTS</h2>
<div class="abs rule"></div>
<p class="abs lead">Here are some of the projects we've created over the years.</p>

<div class="abs tile t-metal" style="left:53px;top:396px;width:119px;height:165px" role="img" aria-label="Machined aluminium rings and discs on wood"></div>
<div class="abs tile t-dark" style="left:177px;top:396px;width:120px;height:165px" role="img" aria-label="Close-up of a black anodized machined part"></div>
<div class="abs tile t-tri" style="left:302px;top:396px;width:119px;height:165px" role="img" aria-label="Grid of triangular machined components"></div>
<div class="abs tile t-pins" style="left:425px;top:396px;width:244px;height:165px" role="img" aria-label="Plate with rows of cylindrical pins"></div>
<div class="abs tile t-chips" style="left:53px;top:567px;width:244px;height:165px" role="img" aria-label="Pile of metal machining chips"></div>
<div class="abs tile t-holes" style="left:301px;top:567px;width:119px;height:165px" role="img" aria-label="Perforated disc with radial pattern"></div>
<div class="abs tile t-brass" style="left:425px;top:567px;width:120px;height:165px" role="img" aria-label="Brass machined blocks on blue surface"></div>
<div class="abs tile t-coil" style="left:549px;top:567px;width:120px;height:165px" role="img" aria-label="Blue tinted metal coil shavings"></div>

<div class="abs load">LOAD MORE</div>

<footer class="abs footer"></footer>
<svg class="abs callband" width="723" height="76" viewBox="0 0 723 76">
  <polygon points="388,0 723,0 723,21 397,21" fill="#141414"/>
  <polygon points="397,21 723,21 723,75 420,75" fill="#59ff00"/>
</svg>
<div class="abs foot-brand">TARN LOCK</div>
<p class="abs foot-about">Velkrin Manufacturing has humble<br>roots, starting as many machine</p>
<div class="abs call-icon"><svg width="11" height="11" viewBox="0 0 24 24"><path fill="#fff" d="M6.6 10.8a15 15 0 0 0 6.6 6.6l2.2-2.2a1 1 0 0 1 1-.25 11.4 11.4 0 0 0 3.6.57 1 1 0 0 1 1 1V20a1 1 0 0 1-1 1A17 17 0 0 1 3 4a1 1 0 0 1 1-1h3.5a1 1 0 0 1 1 1c0 1.25.2 2.45.57 3.57a1 1 0 0 1-.25 1z"/></svg></div>
<div class="abs call-label">Call us:</div>
<div class="abs call-num">+123 456 7890</div>

<h3 class="abs col-head display" style="left:87px">HELPFUL LINKS</h3>
<h3 class="abs col-head display" style="left:226px">INFORMATION</h3>
<h3 class="abs col-head display" style="left:338px">CONTACT US</h3>
<h3 class="abs col-head display" style="left:483px">GET IN TOUCH</h3>

<ul class="abs links">
  <li>Why velkrin manufacturing?</li><li>What We Do</li><li>How We Make It Better</li><li>Capabilities</li><li>Gallery</li><li>About Us</li><li>Wisdom</li><li>Contact Us</li>
</ul>

<div class="abs social" style="top:1015px"><i></i>Facebook</div>
<div class="abs social" style="top:1036px"><i></i>Twitter</div>
<div class="abs social" style="top:1057px"><i></i>Google</div>
<div class="abs social" style="top:1079px"><i></i>Linkedin</div>
<div class="abs social" style="top:1101px"><i></i>Youtube</div>

<div class="abs contact-item" style="top:1017px">
  <svg width="9" height="8" viewBox="0 0 24 20"><path fill="#59ff00" d="M2 2h20v16H2z"/><path fill="#0c0c0c" d="M2 2l10 8 10-8z"/></svg>
  <div>Email:<br>info@tarnlock.com</div>
</div>
<div class="abs contact-item" style="top:1049px">
  <svg width="9" height="9" viewBox="0 0 24 24"><path fill="#59ff00" d="M6.6 10.8a15 15 0 0 0 6.6 6.6l2.2-2.2a1 1 0 0 1 1-.25 11.4 11.4 0 0 0 3.6.57 1 1 0 0 1 1 1V20a1 1 0 0 1-1 1A17 17 0 0 1 3 4a1 1 0 0 1 1-1h3.5a1 1 0 0 1 1 1c0 1.25.2 2.45.57 3.57a1 1 0 0 1-.25 1z"/></svg>
  <div>Phone:<br>+08 123 456 7890</div>
</div>
<div class="abs contact-item" style="top:1081px">
  <svg width="8" height="10" viewBox="0 0 20 26"><path fill="#59ff00" d="M10 0a9 9 0 0 0-9 9c0 7 9 17 9 17s9-10 9-17a9 9 0 0 0-9-9zm0 12a3 3 0 1 1 0-6 3 3 0 0 1 0 6z"/></svg>
  <div>Location:<br>Some address line goes<br>here city name</div>
</div>

<div class="abs field" style="top:1015px">Enter Name</div>
<div class="abs field" style="top:1039px">Enter Company</div>
<div class="abs field" style="top:1064px">Enter Country</div>
<div class="abs submit">SUBMIT</div>

<div class="abs divider"></div>
<p class="abs copy">©COPYRIGHT 2022 TARN LOCK, ALL RIGHTS RESERVED</p>
<div class="abs top-btn"><svg width="8" height="10" viewBox="0 0 8 10"><path d="M4 10V1M1 4l3-3 3 3" stroke="#111" stroke-width="0.8" fill="none"/></svg></div>

</body>
</html>
```